Business Card Design for Occupational Medicine Start Up Company

We need to design a professional business card. We are a healthcare company providing occupational medicine services to blue collar industries. We are professional, efficient and high quality service providers.

Target Market(s)

Blue Collar Industry: Shipbuilding, Ports, Trucking Companies; The Executives and Safety Officers for these companies

Industry/Entity Type

Healthcare

Contact Information for Business Card

Logo, Name, Title, Email, Phone

Other font styles liked:
• Please match our Brand Guide

Requirements
Must have
• Our Company Colors and Logo

```html
<!DOCTYPE html>
<html lang="en">
<head>
<meta charset="utf-8">
<title>CrewWell Clinics – Business Card</title>
<link href="https://fonts.googleapis.com/css2?family=Montserrat:wght@700&family=Poppins:wght@400;700&display=swap" rel="stylesheet">
<style>
  :root {
    --navy: #283386;
    --navy-soft: #2e3a96;
    --ink: #1b1b1b;
    --rule: #9a9a9a;
    --paper: #ffffff;
    --backdrop: #b9b9b9;
    --accent: #f2b34c;
  }
  * { box-sizing: border-box; margin: 0; padding: 0; }
  html, body { width: 1200px; height: 1200px; overflow: hidden; }
  body {
    background: var(--backdrop);
    font-family: "Poppins", sans-serif;
    position: relative;
  }
  .card {
    position: absolute;
    top: 303px;
    width: 368px;
    height: 594px;
    box-shadow: 3px 4px 6px rgba(0,0,0,.35);
  }
  .card-back { left: 200px; background: var(--navy); overflow: hidden; }
  .card-front { left: 599px; background: var(--paper); }

  .back-texture {
    position: absolute; inset: 0;
    background: radial-gradient(circle at 50% 45%, var(--navy-soft) 0%, var(--navy) 70%);
  }
  .wordmark {
    position: absolute; left: 0; right: 0;
    text-align: center;
    font-family: "Montserrat", sans-serif;
    font-weight: 700;
    line-height: 1;
  }
  .wordmark .name { display: block; font-size: 33px; letter-spacing: .5px; }
  .wordmark .sub { display: block; font-size: 20px; letter-spacing: 8px; margin-top: 6px; padding-left: 8px; }
  .card-back .wordmark { top: 486px; color: var(--paper); }
  .card-front .wordmark { top: 194px; color: var(--navy); }

  .mark-dot {
    position: absolute; left: 159px; top: 90px;
    width: 50px; height: 50px; border-radius: 50%;
    background: var(--navy);
  }
  .person { position: absolute; top: 336px; left: 0; right: 0; text-align: center; }
  .person-name { font-weight: 700; font-size: 26px; color: var(--navy); letter-spacing: .5px; line-height: 1; }
  .person-title { font-size: 16px; color: var(--ink); margin-top: 2px; }

  .icon-row {
    position: absolute; top: 394px; left: 87px; width: 190px; height: 26px;
    display: flex; align-items: center; gap: 4px;
  }
  .icon-row .rule { flex: 1; height: 1px; background: var(--rule); }
  .icon-row .icon { width: 25px; height: 25px; border-radius: 3px; background: var(--navy); display: flex; align-items: center; justify-content: center; }
  .icon-row .icon:first-of-type { margin-left: 4px; }
  .icon-row .icon:last-of-type { margin-right: 4px; }

  .contact { position: absolute; top: 428px; left: 0; right: 0; text-align: center; font-size: 16.5px; color: var(--ink); line-height: 21px; }
  .divider { position: absolute; top: 507px; left: 88px; width: 195px; height: 1px; background: var(--rule); }
  .address { position: absolute; top: 519px; left: 0; right: 0; text-align: center; font-size: 16.5px; color: var(--ink); line-height: 21px; }
</style>
</head>
<body>
  <section class="card card-back">
    <div class="back-texture" role="img" aria-label="Faint repeating brand-symbol pattern in deep blue"></div>
    <div class="wordmark">
      <span class="name">CREWWELL</span>
      <span class="sub">CLINICS</span>
    </div>
  </section>

  <section class="card card-front">
    <div class="mark-dot"></div>
    <div class="wordmark">
      <span class="name">CREWWELL</span>
      <span class="sub">CLINICS</span>
    </div>

    <div class="person">
      <p class="person-name">DANIEL MORENO</p>
      <p class="person-title">Managing Director</p>
    </div>

    <div class="icon-row">
      <span class="rule"></span>
      <span class="icon" aria-label="Phone">
        <svg width="15" height="13" viewBox="0 0 15 13"><path d="M1 4 Q7.5 -1 14 4 L12 6 L10 4.5 L10 3.5 Q7.5 2.5 5 3.5 L5 4.5 L3 6 Z M3 7 L12 7 L13 12 L2 12 Z" fill="#fff"/></svg>
      </span>
      <span class="icon" aria-label="Email">
        <svg width="15" height="11" viewBox="0 0 15 11"><rect x=".5" y=".5" width="14" height="10" fill="none" stroke="#fff"/><path d="M.5 .5 L7.5 6 L14.5 .5" fill="none" stroke="#fff"/></svg>
      </span>
      <span class="icon" aria-label="Website">
        <svg width="15" height="15" viewBox="0 0 15 15"><circle cx="7.5" cy="7.5" r="6.5" fill="#fff"/><path d="M4 5 Q6 3 8 5 Q7 8 5 8 Z M9 9 Q11 8 12 10 Q10 12 9 11 Z" fill="#283386"/></svg>
      </span>
      <span class="rule"></span>
    </div>

    <div class="contact">
      <p>044-555 010 234</p>
      <p>info@crewwellmail.com</p>
      <p>www.crewwellclinics.com</p>
    </div>

    <div class="divider"></div>

    <div class="address">
      <p>421, Address line goes here</p>
      <p>45452,Country Name</p>
    </div>
  </section>
</body>
</html>
```